New Word Template Design Project

I need this document for death certificate ordering to look like our branding. I will attach the pdf with the information and a sample pdf of our style. I also think that check boxes and x's would be better than yes and no.

2nd page in spanish.

Industry/Entity Type

Funeral

Requirements
Should not have
• Check boxes and red x's or yellow next to the yes, no , or sometimes

```html
<!DOCTYPE html>
<html lang="en">
<head>
<meta charset="utf-8">
<title>Death Certificate Ordering Guide</title>
<link href="https://fonts.googleapis.com/css2?family=Jost:wght@400;500;600&display=swap" rel="stylesheet">
<style>
:root{
  --brand-blue:#4f83a6;
  --header-blue:#5585a5;
  --ink:#222;
  --rule:#9aa5b4;
  --gold:#d4a33a;
  --lilac:#a18db8;
  --paper:#fff;
}
*{box-sizing:border-box;margin:0;padding:0}
html,body{width:928px;height:1200px;overflow:hidden;background:var(--paper)}
body{font-family:"Jost",sans-serif;color:var(--ink);position:relative}
.page{position:absolute;inset:0;background:var(--paper)}
.title{position:absolute;left:68px;top:92px;font-size:27px;font-weight:600;color:var(--brand-blue);letter-spacing:.2px}
.brand{position:absolute;right:66px;top:66px;display:flex;align-items:center;gap:8px;color:var(--brand-blue);font-size:19px;font-weight:500}
.brand-dot{width:12px;height:12px;border-radius:50%;background:var(--brand-blue)}
.subtitle{position:absolute;left:68px;font-size:16.5px;font-weight:400}
.subtitle.guide{top:145px}
.subtitle.county{top:180px}
.text{position:absolute;left:68px;width:797px;font-size:12.6px;line-height:17.7px}
.intro{top:224px}
.text b{font-weight:600}
.text em{font-weight:600;font-style:italic}
table.uses{position:absolute;left:68px;top:302px;width:795px;border-collapse:collapse;font-size:13px}
.uses th{background:var(--header-blue);color:#fff;font-weight:500;height:27px;text-align:center;font-size:13px}
.uses th:first-child{text-align:left;padding-left:14px}
.uses td{height:26.6px;border:1px solid var(--rule);padding:0 0 0 13px;white-space:nowrap}
.uses td.qty{text-align:center;padding:0}
.uses col.use{width:317px}.uses col.mid{width:159px}
.cell{display:flex;align-items:center;gap:9px;padding-left:3px}
.icon{width:15px;height:15px;flex:none}
.block-pricing{top:745px}
.block-travel{top:800px}
.block-note{top:871px}
.block-most{top:925px}
.block-ask{top:974px}
.block-contact{top:1044px}
ul.list{list-style:none}
ul.list li{position:relative;padding-left:25px}
ul.list li::before{content:"";position:absolute;left:2px;top:5px;width:8px;height:8px;border-radius:50%;background:var(--brand-blue)}
.band{position:absolute;left:0;bottom:0;width:928px;height:36px;background:linear-gradient(90deg,var(--brand-blue),var(--lilac) 50%,var(--gold))}
</style>
</head>
<body>
<svg width="0" height="0" style="position:absolute">
  <defs>
    <symbol id="tick" viewBox="0 0 16 16"><rect width="16" height="16" rx="3" fill="#5585a5"/><path d="M4 8.3l2.7 2.7L12 5.4" stroke="#fff" stroke-width="2" fill="none" stroke-linecap="round" stroke-linejoin="round"/></symbol>
    <symbol id="cross" viewBox="0 0 16 16"><path d="M2.5 2.5l11 11M13.5 2.5l-11 11" stroke="#d4a33a" stroke-width="2.6" stroke-linecap="round"/></symbol>
  </defs>
</svg>
<main class="page">
  <h1 class="title">Hollis Brook Funeral &amp; Cremation Services</h1>
  <div class="brand"><span class="brand-dot"></span>Hollis Brook</div>
  <p class="subtitle guide">Death Certificate Ordering Guide</p>
  <p class="subtitle county">Miami-Dade County</p>

  <p class="text intro">Certified death certificates are used to handle legal, financial, and personal matters after a loved one passes. While some institutions require an original, others may only need to view or copy it. In Florida, you can order death certificates <em>with</em> or <em>without</em> the cause of death. Cause of death is confidential and should only be included when necessary.</p>

  <table class="uses">
    <colgroup><col class="use"><col class="mid"><col class="mid"><col></colgroup>
    <thead><tr><th>Use</th><th>Original Needed?</th><th>With Cause?</th><th>Suggested Quantity</th></tr></thead>
    <tbody>
      <tr><td>Life Insurance Claims</td><td><div class="cell"><svg class="icon"><use href="#tick"/></svg>Yes</div></td><td><div class="cell"><svg class="icon"><use href="#tick"/></svg>Yes</div></td><td class="qty">1 per policy</td></tr>
      <tr><td>Pension or Retirement Benefits</td><td><div class="cell"><svg class="icon"><use href="#tick"/></svg>Yes</div></td><td><div class="cell"><svg class="icon"><use href="#tick"/></svg>Yes</div></td><td class="qty">1</td></tr>
      <tr><td>Bank Accounts</td><td><div class="cell"><svg class="icon"><use href="#cross"/></svg>Usually Not</div></td><td><div class="cell"><svg class="icon"><use href="#cross"/></svg>No</div></td><td class="qty">0–1</td></tr>
      <tr><td>Investment / Brokerage Accounts</td><td><div class="cell"><svg class="icon"><use href="#tick"/></svg>Sometimes</div></td><td><div class="cell"><svg class="icon"><use href="#tick"/></svg>Sometimes</div></td><td class="qty">1–2</td></tr>
      <tr><td>Vehicle Title Transfer (DMV)</td><td><div class="cell"><svg class="icon"><use href="#tick"/></svg>Yes</div></td><td><div class="cell"><svg class="icon"><use href="#cross"/></svg>No</div></td><td class="qty">1</td></tr>
      <tr><td>Property / Real Estate Transfers</td><td><div class="cell"><svg class="icon"><use href="#tick"/></svg>Yes</div></td><td><div class="cell"><svg class="icon"><use href="#cross"/></svg>No</div></td><td class="qty">1 per property</td></tr>
      <tr><td>Probate / Court Matters</td><td><div class="cell"><svg class="icon"><use href="#tick"/></svg>Yes</div></td><td><div class="cell"><svg class="icon"><use href="#tick"/></svg>Often</div></td><td class="qty">1–2</td></tr>
      <tr><td>Social Security / Government Benefits</td><td><div class="cell"><svg class="icon"><use href="#cross"/></svg>No</div></td><td><div class="cell"><svg class="icon"><use href="#cross"/></svg>No</div></td><td class="qty">0</td></tr>
      <tr><td>Passport Cancellation / Consulates</td><td><div class="cell"><svg class="icon"><use href="#tick"/></svg>Yes</div></td><td><div class="cell"><svg class="icon"><use href="#tick"/></svg>Yes</div></td><td class="qty">1</td></tr>
      <tr><td>Domestic Travel with Cremated Remains</td><td><div class="cell"><svg class="icon"><use href="#tick"/></svg>Yes</div></td><td><div class="cell"><svg class="icon"><use href="#cross"/></svg>No</div></td><td class="qty">1</td></tr>
      <tr><td>International Travel with Cremated Remains</td><td><div class="cell"><svg class="icon"><use href="#tick"/></svg>Yes</div></td><td><div class="cell"><svg class="icon"><use href="#tick"/></svg>Sometimes</div></td><td class="qty">1</td></tr>
      <tr><td>Domestic Forwarding of Remains</td><td><div class="cell"><svg class="icon"><use href="#tick"/></svg>Yes</div></td><td><div class="cell"><svg class="icon"><use href="#cross"/></svg>No</div></td><td class="qty">1</td></tr>
      <tr><td>International Forwarding of Remains</td><td><div class="cell"><svg class="icon"><use href="#tick"/></svg>Yes</div></td><td><div class="cell"><svg class="icon"><use href="#tick"/></svg>Yes</div></td><td class="qty">1</td></tr>
      <tr><td>Credit Cards / Utility Companies</td><td><div class="cell"><svg class="icon"><use href="#cross"/></svg>Usually Not</div></td><td><div class="cell"><svg class="icon"><use href="#cross"/></svg>No</div></td><td class="qty">0</td></tr>
      <tr><td>Personal Copy / Peace of Mind</td><td><div class="cell"><svg class="icon"><use href="#cross"/></svg>Optional</div></td><td><div class="cell"><svg class="icon"><use href="#tick"/></svg>Optional</div></td><td class="qty">1</td></tr>
    </tbody>
  </table>

  <div class="text block-pricing"><b>Pricing (Miami-Dade County):</b><br>The first certified death certificate is <em>$20</em>, and each additional copy is <em>$16</em>.</div>
  <p class="text block-travel">If you are <b>traveling domestically</b> or <b>internationally with cremated remains</b>, at least one certified copy is typically required. Some countries may require the certificate <b>with cause of death.</b> We will reach out to the consulate of the destination country to confirm the specific requirements for transporting cremated remains.</p>
  <p class="text block-note">Please note: <b>Other counties may have different pricing</b> for death certificates. We will inform you of the exact cost based on the location of death.</p>
  <p class="text block-most"><b>Most families order 4 to 8 certified copies.</b> A mix is common — for example, 2 with cause and 4 without cause. It simpler and more cost-effective to order them at the time of need. If you're unsure, we are here to guide you through the process.</p>
  <div class="text block-ask"><b>How many certified copies would you like to order?</b>
    <ul class="list"><li>With Cause of Death</li><li>Without Cause of Death</li></ul></div>
  <div class="text block-contact"><b>Questions? We’re Here for You</b>
    <ul class="list"><li>(305) 555-0142</li><li>kendall@hollisbrook.com | midtown@hollisbrook.com | coralgables@hollisbrook.com | preplanning@hollisbrook.com Serving Miami-Dade County with care, dignity, and support for over 100 years.</li></ul></div>

  <div class="band"></div>
</main>
</body>
</html>
```